VELMOR Website Design

We need a website designed for our company VELMOR. We are a luxury lifestyle club that will provide benefits and services for our members. The site should be clean & sleek, preferably using black and white (or darker colors). (example sites: stravenhall.example, plinth.example)

Here is a link of a sample page I did using wix. (https://dunmere7.sitehostly.example/mysite) This can be used to get a general idea.

Target Market(s)

Upper Middle Class in the United States

Number of Pages Required

5+ page

Font styles to use
Sans Serif
Other font styles liked:
• Arial (or other similar fonts)

Requirements
Must have
• A clean design that is eye-catching and speaks to our company.
Nice to have
• Ideas for copy.

```html
<!DOCTYPE html>
<html lang="en">
<head>
<meta charset="utf-8">
<title>VELMOR — Services &amp; Benefits</title>
<link rel="stylesheet" href="https://fonts.googleapis.com/css2?family=Montserrat:wght@400;500;600;700&display=swap">
<style>
:root{
  --page:#232323;
  --panel:#1b1b1b;
  --panel-line:#2e2e2e;
  --accent:#0a62e6;
  --accent-soft:#2f7cf0;
  --white:#ffffff;
  --text:#e6e6e6;
  --muted:#8a8a8a;
  --dim:#6a6a6a;
  --footer-bar:#191919;
}
*{box-sizing:border-box;margin:0;padding:0}
html,body{width:1200px;height:2628px;overflow:hidden}
body{background:var(--page);font-family:"Montserrat",Arial,sans-serif;color:var(--text);position:relative}
.abs{position:absolute}

/* header */
.hero{left:0;top:0;width:1200px;height:242px;background:linear-gradient(120deg,#3a4450 0%,#5b6876 35%,#7d8995 55%,#4a5460 80%,#2c333c 100%)}
.hero-shade{left:0;top:0;width:1200px;height:242px;background:rgba(20,24,30,.45)}
.brand{left:119px;top:26px;height:48px;display:flex;align-items:center;font-size:38px;font-weight:500;letter-spacing:2px;color:var(--white)}
.nav{left:722px;top:40px;display:flex;gap:22px;align-items:center;font-size:13px;font-weight:500;color:var(--white)}
.nav a{color:inherit;text-decoration:none}
.nav .current{color:var(--accent-soft)}
.nav .section{border-bottom:2px solid var(--white);padding-bottom:3px}
.nav .search{width:22px;height:22px;border-radius:50%;background:var(--accent);display:flex;align-items:center;justify-content:center}
.page-title{left:112px;top:128px;font-size:30px;font-weight:600;color:var(--white);letter-spacing:.5px}

/* posts */
.post{left:112px;width:724px;height:488px;background:var(--panel)}
.post-image{width:724px;height:289px}
.post-body{position:relative;height:199px}
.post-mark{position:absolute;left:14px;top:19px;width:70px;height:70px;border:2px solid var(--accent);background:#141414}
.post-text{position:absolute;left:103px;top:16px;width:600px}
.post-kicker{font-size:10px;font-weight:700;color:var(--white);letter-spacing:.3px}
.post-title{font-size:21px;font-weight:600;color:var(--white);margin-top:8px;letter-spacing:.3px}
.post-meta{font-size:9.5px;color:var(--text);margin-top:4px}
.post-excerpt{font-size:10.5px;line-height:24px;color:var(--text);margin-top:10px}
.post-more{font-size:10px;color:var(--white);margin-top:4px;font-weight:500}

/* sidebar */
.categories{left:862px;top:293px;width:224px;background:var(--accent)}
.categories h3{font-size:14px;font-weight:600;color:var(--white);padding:10px 10px 9px;border-bottom:1px solid rgba(255,255,255,.35)}
.categories li{list-style:none;font-size:10.5px;color:var(--white);height:36px;line-height:36px;padding-left:10px;border-bottom:1px solid rgba(255,255,255,.3)}
.popular{left:862px;top:574px;width:224px;height:424px;background:var(--panel)}
.side-heading{font-size:14px;font-weight:500;color:#b0b0b0;letter-spacing:.5px}
.popular .side-heading{padding:14px 12px 0}
.event{position:absolute;left:0;width:224px;height:74px;padding:10px 0 0 14px;display:flex;gap:12px}
.event.active{border-left:3px solid var(--accent);background:#1f1f1f}
.event-date{color:var(--accent-soft);font-weight:700;font-size:19px;line-height:18px;width:28px;text-align:center}
.event-date small{display:block;font-size:10px;font-weight:600}
.event-info{font-size:10.5px;color:var(--dim);line-height:16px;width:150px}
.event.active .event-info{color:var(--accent-soft)}
.event-time{color:var(--white);font-size:9.5px;margin-top:6px;display:flex;align-items:center;gap:5px}
.archives{left:872px;top:1024px;width:214px}
.archives ul{margin-top:10px}
.archives li{list-style:none;height:40px;line-height:40px;font-size:10.5px;color:var(--dim);display:flex;align-items:center;gap:10px}
.archives li.active{color:var(--accent-soft)}
.tags{left:872px;top:1362px;width:214px}
.tag-list{display:flex;flex-wrap:wrap;gap:6px;margin-top:12px;width:220px}
.tag{font-size:9.5px;color:#c8c8c8;background:#2d2d2d;padding:6px 8px}
.tag.active{background:var(--accent);color:var(--white)}
.underline{width:80px;height:1px;background:var(--accent);margin-top:6px}

/* pagination */
.pager{left:112px;top:2355px;display:flex;gap:8px}
.pager span{width:26px;height:26px;border:1px solid #555;display:flex;align-items:center;justify-content:center;font-size:11px;color:var(--white)}
.pager .current{background:var(--accent);border-color:var(--accent)}

/* footer */
.footer-col{top:2452px;font-size:10px;line-height:17px;color:var(--white)}
.footer-col h4{font-size:11px;font-weight:600;color:var(--accent-soft);margin-bottom:10px}
.footer-col .hl{color:var(--accent-soft)}
.socials{left:114px;top:2510px;display:flex;gap:12px}
.socials span{width:26px;height:26px;border:1px solid #777;border-radius:50%}
.subscribe{left:781px;top:2518px;width:144px;height:28px;border:1px solid #666;border-radius:14px;display:flex;align-items:center;justify-content:space-between;padding:0 10px 0 14px;font-size:9.5px;color:var(--muted)}
.footer-bar{left:0;top:2582px;width:1200px;height:46px;background:var(--footer-bar);display:flex;align-items:center;justify-content:center}
</style>
</head>
<body>

<header>
  <div class="abs hero" role="img" aria-label="Upward view of glass office towers against the sky"></div>
  <div class="abs hero-shade"></div>
  <div class="abs brand">VELMOR</div>
  <nav class="abs nav">
    <a class="current">Home</a>
    <a>About us</a>
    <a class="section">Services &amp; Benefits</a>
    <a>Contact</a>
    <span class="search"><svg width="10" height="10" viewBox="0 0 10 10"><circle cx="4" cy="4" r="3" fill="none" stroke="#fff" stroke-width="1.5"/><line x1="6.2" y1="6.2" x2="9" y2="9" stroke="#fff" stroke-width="1.5"/></svg></span>
  </nav>
  <h1 class="abs page-title">SERVICES &amp; BENEFITS</h1>
</header>

<main>
  <article class="abs post" style="top:293px">
    <div class="post-image" role="img" aria-label="Ballroom event hall lit in purple and blue with guests" style="background:linear-gradient(135deg,#3a1f6e,#6c3bb8 40%,#2b5fb8 70%,#1b2550)"></div>
    <div class="post-body"><div class="post-mark"></div><div class="post-text">
      <div class="post-kicker">SUCCESS STORIES</div><h2 class="post-title">EVENT SERVICE</h2>
      <div class="post-meta">By Lena Harwick &nbsp;On 5 October, 2014 in Success Stories</div>
      <p class="post-excerpt">Lorem ipsum dolor sit amet, consectetur adipiscing elit. Mauris finibus maximus lorem ut scelerisque. Nulla facilisi. Fusce sagittis quis massa at consequat. Pellentesque orci risus, congue quis interdum quis, aliquet ut turpis.</p>
      <div class="post-more">Read more</div></div></div>
  </article>

  <article class="abs post" style="top:809px">
    <div class="post-image" role="img" aria-label="Compass dial pointing toward the word invest" style="background:linear-gradient(160deg,#f2f2f2,#d9dadd 50%,#b8b2a6)"></div>
    <div class="post-body"><div class="post-mark"></div><div class="post-text">
      <div class="post-kicker">SUCCESS STORIES</div><h2 class="post-title">INVESTMENT SERVICE</h2>
      <div class="post-meta">By Lena Harwick &nbsp;On 5 October, 2014 in Success Stories</div>
      <p class="post-excerpt">Lorem ipsum dolor sit amet, consectetur adipiscing elit. Mauris finibus maximus lorem ut scelerisque. Nulla facilisi. Fusce sagittis quis massa at consequat. Pellentesque orci risus, congue quis interdum quis, aliquet ut turpis.</p>
      <div class="post-more">Read more</div></div></div>
  </article>

  <article class="abs post" style="top:1330px">
    <div class="post-image" role="img" aria-label="Hands reviewing financial charts beside a laptop" style="background:linear-gradient(120deg,#cfd6dd,#e9ecef 40%,#9a8f82 75%,#4d4a48)"></div>
    <div class="post-body"><div class="post-mark"></div><div class="post-text">
      <div class="post-kicker">SUCCESS STORIES</div><h2 class="post-title">ACCOUNTING SERVICE</h2>
      <div class="post-meta">By Lena Harwick &nbsp;On 5 October, 2014 in Success Stories</div>
      <p class="post-excerpt">Lorem ipsum dolor sit amet, consectetur adipiscing elit. Mauris finibus maximus lorem ut scelerisque. Nulla facilisi. Fusce sagittis quis massa at consequat. Pellentesque orci risus, congue quis interdum quis, aliquet ut turpis.</p>
      <div class="post-more">Read more</div></div></div>
  </article>

  <article class="abs post" style="top:1848px">
    <div class="post-image" role="img" aria-label="Two business people shaking hands" style="background:linear-gradient(110deg,#1e1e22,#3b3b40 30%,#c9a48c 50%,#5d6a80 75%,#1c2230)"></div>
    <div class="post-body"><div class="post-mark"></div><div class="post-text">
      <div class="post-kicker">SUCCESS STORIES</div><h2 class="post-title">LAWYER SERVICE</h2>
      <div class="post-meta">By Lena Harwick &nbsp;On 5 October, 2014 in Success Stories</div>
      <p class="post-excerpt">Lorem ipsum dolor sit amet, consectetur adipiscing elit. Mauris finibus maximus lorem ut scelerisque. Nulla facilisi. Fusce sagittis quis massa at consequat. Pellentesque orci risus, congue quis interdum quis, aliquet ut turpis.</p>
      <div class="post-more">Read more</div></div></div>
  </article>

  <div class="abs pager"><span>&lsaquo;</span><span class="current">1</span><span>2</span><span>3</span><span>&rsaquo;</span></div>
</main>

<aside>
  <section class="abs categories">
    <h3>EVENTS CATEGORIES</h3>
    <ul>
      <li>Seminars and Conferences Events</li>
      <li>Trade Shows Events</li>
      <li>Executive Retreats Events</li>
      <li>Appreciation Events</li>
      <li>Product Launch Events</li>
      <li style="border-bottom:0">Team-Building &nbsp;Events</li>
    </ul>
  </section>

  <section class="abs popular">
    <h3 class="side-heading">POPULAR EVENTS</h3>
    <div class="event" style="top:40px"><div class="event-date">25<small>SEP</small></div><div class="event-info">Repeating month event<div class="event-time"><svg width="9" height="9" viewBox="0 0 10 10"><circle cx="5" cy="5" r="4" fill="none" stroke="#fff"/><path d="M5 3v2h2" stroke="#fff" fill="none"/></svg>8:00 AM- 10:00 AM</div></div></div>
    <div class="event active" style="top:118px"><div class="event-date">25<small>SEP</small></div><div class="event-info">Lorem ipsum dolor sit a met, consectetur<div class="event-time"><svg width="9" height="9" viewBox="0 0 10 10"><circle cx="5" cy="5" r="4" fill="none" stroke="#fff"/><path d="M5 3v2h2" stroke="#fff" fill="none"/></svg>8:00 AM- 10:00 AM</div></div></div>
    <div class="event" style="top:196px"><div class="event-date">25<small>SEP</small></div><div class="event-info">Cras commodo suscipit<div class="event-time"><svg width="9" height="9" viewBox="0 0 10 10"><circle cx="5" cy="5" r="4" fill="none" stroke="#fff"/><path d="M5 3v2h2" stroke="#fff" fill="none"/></svg>8:00 AM- 10:00 AM</div></div></div>
    <div class="event" style="top:274px"><div class="event-date">25<small>SEP</small></div><div class="event-info">Nunc imperdiet libero sapien, ut faucibus mag<div class="event-time"><svg width="9" height="9" viewBox="0 0 10 10"><circle cx="5" cy="5" r="4" fill="none" stroke="#fff"/><path d="M5 3v2h2" stroke="#fff" fill="none"/></svg>8:00 AM- 10:00 AM</div></div></div>
    <div class="event" style="top:352px"><div class="event-date">25<small>SEP</small></div><div class="event-info">Mauris id commodo dolor<div class="event-time"><svg width="9" height="9" viewBox="0 0 10 10"><circle cx="5" cy="5" r="4" fill="none" stroke="#fff"/><path d="M5 3v2h2" stroke="#fff" fill="none"/></svg>8:00 AM- 10:00 AM</div></div></div>
  </section>

  <section class="abs archives">
    <h3 class="side-heading">ARCHIVES</h3>
    <div class="underline"></div>
    <ul>
      <li><svg width="10" height="10" viewBox="0 0 10 10"><rect x="1" y="2" width="8" height="7" fill="none" stroke="currentColor"/><line x1="1" y1="4" x2="9" y2="4" stroke="currentColor"/></svg>January 2014</li>
      <li><svg width="10" height="10" viewBox="0 0 10 10"><rect x="1" y="2" width="8" height="7" fill="none" stroke="currentColor"/><line x1="1" y1="4" x2="9" y2="4" stroke="currentColor"/></svg>September 2013</li>
      <li class="active"><svg width="10" height="10" viewBox="0 0 10 10"><rect x="1" y="2" width="8" height="7" fill="none" stroke="currentColor"/><line x1="1" y1="4" x2="9" y2="4" stroke="currentColor"/></svg>August 2013</li>
      <li><svg width="10" height="10" viewBox="0 0 10 10"><rect x="1" y="2" width="8" height="7" fill="none" stroke="currentColor"/><line x1="1" y1="4" x2="9" y2="4" stroke="currentColor"/></svg>July 2013</li>
      <li><svg width="10" height="10" viewBox="0 0 10 10"><rect x="1" y="2" width="8" height="7" fill="none" stroke="currentColor"/><line x1="1" y1="4" x2="9" y2="4" stroke="currentColor"/></svg>June 2013</li>
      <li><svg width="10" height="10" viewBox="0 0 10 10"><rect x="1" y="2" width="8" height="7" fill="none" stroke="currentColor"/><line x1="1" y1="4" x2="9" y2="4" stroke="currentColor"/></svg>May 2013</li>
      <li><svg width="10" height="10" viewBox="0 0 10 10"><rect x="1" y="2" width="8" height="7" fill="none" stroke="currentColor"/><line x1="1" y1="4" x2="9" y2="4" stroke="currentColor"/></svg>March 2013</li>
    </ul>
  </section>

  <section class="abs tags">
    <h3 class="side-heading">TAGS</h3>
    <div class="underline"></div>
    <div class="tag-list">
      <span class="tag">Doctors</span><span class="tag active">Lorem ipsum</span><span class="tag">fitness</span>
      <span class="tag">boxing trainers</span><span class="tag">health</span><span class="tag">foods</span>
    </div>
  </section>
</aside>

<footer>
  <div class="abs footer-col" style="left:114px">
    <div>Copyright 2017-18 <span class="hl">VELMOR</span></div>
  </div>
  <div class="abs socials"><span></span><span></span><span></span><span></span></div>
  <div class="abs footer-col" style="left:447px;top:2448px">
    <h4>Our location</h4>
    <div>Harbor Lane Holdings LLC 88 Elmcrest,<br>Suite 40 Brookfield, IL 00000</div>
    <div style="margin-top:4px">Phone : +00 1 98765432</div>
    <div style="margin-top:4px">Email : info@velmor.example</div>
  </div>
  <div class="abs footer-col" style="left:781px;top:2448px;width:310px;font-weight:600">
    <h4>Keep in touch</h4>
    <div>Lorem ipsum dolor sit amet, consectetur adi sollicitud ante tellus ornare mi, et mollis</div>
  </div>
  <div class="abs subscribe">Your email<svg width="10" height="10" viewBox="0 0 10 10"><path d="M1 5h7M5 2l3 3-3 3" stroke="#ccc" fill="none" stroke-width="1.4"/></svg></div>
  <div class="abs footer-bar"><svg width="16" height="10" viewBox="0 0 16 10"><path d="M2 8l6-6 6 6" stroke="#fff" stroke-width="2" fill="none"/></svg></div>
</footer>

</body>
</html>
```